Diagram of Hollowmere’s history for website

This project is to design the attached diagram along the lines of the attached image but in our branding - style guide attached. The diagram will be going on the Hollowmere website - www.hollowmere.au.

```html
<!DOCTYPE html>
<html lang="en">
<head>
<meta charset="utf-8">
<title>Our History – Hollowmere</title>
<link href="https://fonts.googleapis.com/css2?family=Poppins:wght@400;500;600&display=swap" rel="stylesheet">
<style>
  :root {
    --ink: #333333;
    --text: #3f3f3f;
    --band: #e2e9e9;
    --c2017: #687e80;
    --c2018: #84a0a6;
    --c2019: #566f57;
    --c2021: #6d8f72;
    --c2022: #a98a7c;
    --c2023: #d5ab95;
    --paper: #ffffff;
  }
  * { box-sizing: border-box; margin: 0; padding: 0; }
  html, body { width: 1200px; height: 708px; overflow: hidden; background: var(--paper); }
  body { font-family: "Poppins", sans-serif; color: var(--text); }
  .history { position: relative; width: 1200px; height: 708px; }

  .brand { position: absolute; left: 134px; top: 76px; display: flex; align-items: center; gap: 8px;
    font-weight: 600; font-size: 18px; color: var(--c2018); }
  .brand-dot { width: 14px; height: 14px; border-radius: 50%; background: var(--c2018); }

  .title { position: absolute; left: 93px; top: 144px; font-weight: 600; font-size: 38px; color: var(--ink); letter-spacing: -0.3px; }

  .band { position: absolute; left: 93px; top: 363px; width: 1037px; height: 14px; background: var(--band); }
  .band-arrow { position: absolute; left: 1128px; top: 353px; }

  .stem { position: absolute; width: 1.5px; }
  .dot { position: absolute; width: 22px; height: 22px; border-radius: 50%; transform: translate(-50%, -50%); }

  .event { position: absolute; }
  .event-heading { font-weight: 600; font-size: 16.5px; line-height: 17px; }
  .event-text { font-size: 11.3px; line-height: 13.6px; margin-top: 6px; color: var(--text); }
  .year { position: absolute; font-weight: 600; font-size: 39px; line-height: 1; letter-spacing: -0.5px; }

  .y2017 { color: var(--c2017); } .y2017.stem, .y2017.dot { background: var(--c2017); }
  .y2018 { color: var(--c2018); } .y2018.stem, .y2018.dot { background: var(--c2018); }
  .y2019 { color: var(--c2019); } .y2019.stem, .y2019.dot { background: var(--c2019); }
  .y2021 { color: var(--c2021); } .y2021.stem, .y2021.dot { background: var(--c2021); }
  .y2022 { color: var(--c2022); } .y2022.stem, .y2022.dot { background: var(--c2022); }
  .y2023 { color: var(--c2023); } .y2023.stem, .y2023.dot { background: var(--c2023); }
</style>
</head>
<body>
<main class="history">
  <div class="brand"><span class="brand-dot"></span>Hollowmere</div>
  <h1 class="title">Our History</h1>

  <div class="band"></div>
  <svg class="band-arrow" width="20" height="34" viewBox="0 0 20 34" aria-hidden="true"><polygon points="0,0 20,17 0,34" fill="#e2e9e9"/></svg>

  <!-- 2017 -->
  <div class="stem y2017" style="left:92px;top:370px;height:210px"></div>
  <div class="dot y2017" style="left:93px;top:370px"></div>
  <div class="dot y2017" style="left:93px;top:580px"></div>
  <div class="event y2017" style="left:113px;top:384px;width:200px">
    <h2 class="event-heading">Hollowmere<br>Commences</h2>
    <p class="event-text">Maren started the business with 25 years’ experience working for government &amp; non-government disability &amp;community services. Our first office is in Millbrook</p>
  </div>
  <div class="event y2017" style="left:113px;top:499px;width:200px">
    <h2 class="event-heading">NCSS Provider</h2>
    <p class="event-text">Hollowmere becomes a NCSS Registered provider</p>
  </div>
  <div class="year y2017" style="left:112px;top:561px">2017</div>

  <!-- 2018 -->
  <div class="stem y2018" style="left:262px;top:247px;height:123px"></div>
  <div class="dot y2018" style="left:263px;top:247px"></div>
  <div class="dot y2018" style="left:263px;top:370px"></div>
  <div class="event y2018" style="left:291px;top:236px;width:160px">
    <h2 class="event-heading">Clinic Expansion</h2>
    <p class="event-text">Hollowmere moves offices twice in Millbrook due to growth &amp; expansion. Clinic established</p>
  </div>
  <div class="year y2018" style="left:290px;top:322px">2018</div>

  <!-- 2019 -->
  <div class="stem y2019" style="left:432px;top:370px;height:120px"></div>
  <div class="dot y2019" style="left:432px;top:370px"></div>
  <div class="dot y2019" style="left:432px;top:490px"></div>
  <div class="event y2019" style="left:456px;top:384px;width:160px">
    <h2 class="event-heading">Move to<br>Elmhurst</h2>
    <p class="event-text">Hollowmere moves to Elmhurst due to further growth &amp; expansion</p>
  </div>
  <div class="year y2019" style="left:456px;top:475px">2019</div>

  <!-- 2021 -->
  <div class="stem y2021" style="left:601px;top:234px;height:136px"></div>
  <div class="dot y2021" style="left:602px;top:234px"></div>
  <div class="dot y2021" style="left:602px;top:370px"></div>
  <div class="event y2021" style="left:629px;top:223px;width:200px">
    <h2 class="event-heading">Impact Corporation</h2>
    <p class="event-text">Hollowmere becomes a accredited Impact Corporation having met the highest standards of environmental, social &amp; community performance</p>
  </div>
  <div class="year y2021" style="left:629px;top:322px">2021</div>

  <!-- 2022 -->
  <div class="stem y2022" style="left:771px;top:370px;height:285px"></div>
  <div class="dot y2022" style="left:771px;top:370px"></div>
  <div class="dot y2022" style="left:772px;top:655px"></div>
  <div class="event y2022" style="left:795px;top:384px;width:185px">
    <h2 class="event-heading">Brightwire Best<br>of Business</h2>
    <p class="event-text">Hollowmere wins the Brightwire Best of Business Award (Vic) for building communities</p>
  </div>
  <div class="event y2022" style="left:795px;top:479px;width:185px">
    <h2 class="event-heading">Move to Carrick</h2>
    <p class="event-text">Hollowmere moves to a larger premises in Carrick</p>
  </div>
  <div class="event y2022" style="left:795px;top:548px;width:190px">
    <h2 class="event-heading">Partnership</h2>
    <p class="event-text">Partnerships established with Tarawa Lane School for Children with Disability &amp; Kinfold Centre (Westvale University)</p>
  </div>
  <div class="year y2022" style="left:795px;top:638px">2022</div>

  <!-- 2023 -->
  <div class="stem y2023" style="left:939px;top:52px;height:318px"></div>
  <div class="dot y2023" style="left:940px;top:52px"></div>
  <div class="dot y2023" style="left:940px;top:94px"></div>
  <div class="dot y2023" style="left:940px;top:165px"></div>
  <div class="dot y2023" style="left:940px;top:219px"></div>
  <div class="dot y2023" style="left:940px;top:274px"></div>
  <div class="dot y2023" style="left:940px;top:370px"></div>
  <div class="event y2023" style="left:967px;top:39px;width:200px">
    <h2 class="event-heading">Rebranding</h2>
    <p class="event-text" style="margin-top:4px">Hollowmere rebranded</p>
  </div>
  <div class="event y2023" style="left:967px;top:82px;width:200px">
    <h2 class="event-heading">Community<br>Action Plan (CAP)</h2>
    <p class="event-text">Hollowmere’s Foundation CAP developed &amp; endorsed</p>
  </div>
  <div class="event y2023" style="left:967px;top:153px;width:200px">
    <h2 class="event-heading">Client Advisory Group</h2>
    <p class="event-text">Hollowmere’s Client Advisory Group commences</p>
  </div>
  <div class="event y2023" style="left:967px;top:208px;width:200px">
    <h2 class="event-heading">E-Learning Platform</h2>
    <p class="event-text">Hollowmere e-learning platform launched</p>
  </div>
  <div class="event y2023" style="left:967px;top:262px;width:200px">
    <h2 class="event-heading">Spectrum Mark</h2>
    <p class="event-text">Hollowmere achieves Spectrum Mark accreditation</p>
  </div>
  <div class="year y2023" style="left:967px;top:322px">2023</div>
</main>
</body>
</html>
```